Harborline Auto LLC

Car Dealer Customer Service
Address: 2874 Cresthaven Road, Shelbyville, TN 37162
web: www.harborlineautoxq.net
email: harborlineautoxq@mailnest.example
Phone: (931) 555-0148
Phone: (629) 555-0173

```html
<!DOCTYPE html>
<html lang="en">
<head>
<meta charset="utf-8">
<title>Harborline Auto – Business Card</title>
<link rel="stylesheet" href="https://fonts.googleapis.com/css2?family=Montserrat:wght@400;500;800&display=swap">
<style>
  :root{
    --stage:#3f4246;
    --brand-blue:#1f7db0;
    --accent-blue:#2a90c8;
    --accent-yellow:#edb241;
    --ink:#1b1b1b;
    --paper:#ffffff;
  }
  *{box-sizing:border-box;margin:0;padding:0}
  html,body{width:1200px;height:887px;overflow:hidden}
  body{background:var(--stage);font-family:"Montserrat",sans-serif;position:relative}
  .card{position:absolute;left:290px;width:620px;height:354px;border-radius:22px;overflow:hidden}
  .card--front{top:60px;background:var(--brand-blue)}
  .card--back{top:473px;background:var(--paper)}

  .brand{position:absolute;display:flex;flex-direction:column;align-items:center}
  .brand__dot{width:110px;height:110px;border-radius:50%}
  .brand__name{font-weight:800;letter-spacing:1px;text-transform:uppercase;margin-top:18px;white-space:nowrap}

  .card--front .brand{left:0;right:0;top:70px}
  .card--front .brand__dot{background:var(--paper)}
  .card--front .brand__name{color:var(--paper);font-size:40px}

  .card--back .brand{left:20px;width:290px;top:78px}
  .card--back .brand__dot{background:var(--accent-blue);width:100px;height:100px}
  .card--back .brand__name{color:var(--brand-blue);font-size:26px}

  .divider{position:absolute;left:318px;top:62px;width:2px;height:180px;background:var(--accent-blue)}

  .details{position:absolute;left:338px;top:50px;color:var(--ink);font-size:14px;line-height:1.35}
  .details__role{font-size:15px;font-weight:500;margin-bottom:10px}
  .details__address{margin-bottom:10px}
  .contact{list-style:none}
  .contact li{display:flex;align-items:center;gap:8px;margin-bottom:3px}
  .contact svg{width:14px;height:14px;fill:var(--accent-blue);flex:none}
  .contact .email{font-size:12.5px}
  .web-domain{color:var(--accent-blue)}

  .bands{position:absolute;left:0;bottom:0;width:620px;height:90px}
</style>
</head>
<body>

<section class="card card--front">
  <div class="brand">
    <span class="brand__dot"></span>
    <span class="brand__name">Harborline Auto</span>
  </div>
</section>

<section class="card card--back">
  <div class="brand">
    <span class="brand__dot"></span>
    <span class="brand__name">Harborline Auto</span>
  </div>

  <span class="divider"></span>

  <div class="details">
    <p class="details__role">Car Dealer Customer Service</p>
    <p class="details__address">2874 Cresthaven Road,<br>Shelbyville, TN 37162</p>
    <ul class="contact">
      <li><svg viewBox="0 0 24 24"><path d="M6.6 10.8a15 15 0 0 0 6.6 6.6l2.2-2.2a1 1 0 0 1 1-.25 11.4 11.4 0 0 0 3.6.57 1 1 0 0 1 1 1V20a1 1 0 0 1-1 1A17 17 0 0 1 3 4a1 1 0 0 1 1-1h3.5a1 1 0 0 1 1 1c0 1.25.2 2.45.57 3.57a1 1 0 0 1-.25 1z"/></svg>(931) 555-0148</li>
      <li><svg viewBox="0 0 24 24"><path d="M6.6 10.8a15 15 0 0 0 6.6 6.6l2.2-2.2a1 1 0 0 1 1-.25 11.4 11.4 0 0 0 3.6.57 1 1 0 0 1 1 1V20a1 1 0 0 1-1 1A17 17 0 0 1 3 4a1 1 0 0 1 1-1h3.5a1 1 0 0 1 1 1c0 1.25.2 2.45.57 3.57a1 1 0 0 1-.25 1z"/></svg>(629) 555-0173</li>
      <li><svg viewBox="0 0 24 24"><path d="M2 5h20v14H2z M2 5l10 8 10-8" /></svg><span class="email">harborlineautoxq@mailnest.example</span></li>
      <li><svg viewBox="0 0 24 24"><circle cx="12" cy="12" r="10"/></svg><span>www.<span class="web-domain">harborlineautoxq</span>.net</span></li>
    </ul>
  </div>

  <svg class="bands" viewBox="0 0 620 90" preserveAspectRatio="none" aria-hidden="true">
    <polygon fill="var(--accent-yellow)" points="0,80 412,34 402,90 0,90"/>
    <polygon fill="var(--accent-blue)" points="420,33 620,10 620,90 410,90"/>
  </svg>
</section>

</body>
</html>
```